Marbrook Cupcakes Website

We need a new website. We make Texas-size gourmet cupcakes and cupcake jars. We want a website similar to the one KEYlane is hosting and made. They're charging too much per month. I would like to have Blu Otter host it. see the current site at: marbrookcupcakes.com

```html
<!DOCTYPE html>
<html lang="en">
<head>
<meta charset="utf-8">
<title>Marbrook Cupcakes</title>
<link rel="stylesheet" href="https://fonts.googleapis.com/css2?family=Montserrat:wght@400;500;600;700&family=Great+Vibes&display=swap">
<style>
:root{
  --teal:#72ccd4;
  --teal-deep:#2a96a2;
  --teal-dark:#1f8793;
  --teal-soft:#e7f6f8;
  --ink:#2b2b2b;
  --muted:#555;
  --white:#fff;
}
*{box-sizing:border-box;margin:0;padding:0}
html,body{width:1200px;height:4494px;overflow:hidden}
body{position:relative;background:var(--white);font-family:'Montserrat',sans-serif;color:var(--ink)}
.abs{position:absolute}
.script{font-family:'Great Vibes',cursive;font-weight:400}

/* top bar */
.topbar{left:0;top:0;width:1200px;height:42px;background:var(--teal);color:var(--white);font-size:15px;font-weight:500;display:flex;align-items:center;justify-content:center;gap:14px}
.topbar svg{width:12px;height:15px;vertical-align:-2px;margin-right:4px}
.topbar .sep{width:1px;height:18px;background:var(--white)}

/* header */
.header{left:0;top:42px;width:1200px;height:103px;background:var(--white)}
.brand{left:127px;top:24px;display:flex;align-items:center;gap:12px;color:var(--teal);font-size:30px;font-weight:600;white-space:nowrap}
.brand-dot{width:40px;height:40px;border-radius:50%;background:var(--teal)}
.nav{left:416px;top:65px;display:flex;font-size:15px;font-weight:600;white-space:nowrap}
.nav a{text-decoration:none;color:var(--ink);margin-right:48px}
.nav a.active{color:var(--teal)}
.tools{left:810px;top:18px;display:flex;align-items:center;gap:18px;font-size:16px;font-weight:600;color:var(--teal);white-space:nowrap}
.tools svg{width:18px;height:18px}
.cart{position:relative}
.cart .count{position:absolute;right:-10px;top:-10px;width:16px;height:16px;border-radius:50%;background:var(--teal);color:var(--white);font-size:10px;text-align:center;line-height:16px}

/* hero */
.hero{left:0;top:145px;width:1200px;height:488px;background:linear-gradient(90deg,#2a9aa6,#2793a0 60%,#3aa6b1)}
.hero-brush{left:110px;top:130px;width:480px;height:210px;background:rgba(125,210,218,.75);border-radius:40px 90px 30px 80px;transform:rotate(-4deg)}
.hero-copy{left:110px;top:160px;width:410px;text-align:center;color:var(--white)}
.hero-copy .line{font-size:33px;font-weight:600;letter-spacing:.5px;line-height:42px}
.hero-copy .script{font-size:54px;line-height:52px}
.btn-ghost{display:inline-block;margin-top:22px;border:2px solid var(--white);border-radius:24px;padding:9px 20px;font-size:15px;font-weight:600;color:var(--white);text-decoration:none}
.hero-photo{left:628px;top:45px;width:572px;height:443px;background:radial-gradient(ellipse at 40% 40%,#f4ede0 0,#c9a98a 30%,#6a3f28 55%,rgba(42,150,162,0) 75%)}
.price-badge{left:921px;top:52px;width:122px;height:122px;border-radius:50%;background:#46b2bd;border:4px solid rgba(255,255,255,.55);color:var(--white);text-align:center;padding-top:26px}
.price-badge b{display:block;font-size:24px}
.price-badge span{display:block;font-size:12px;font-weight:600;line-height:14px;margin-top:4px}

/* section headings */
.heading{left:0;width:1200px;text-align:center;font-size:34px;font-weight:600;color:#333;letter-spacing:.5px;white-space:nowrap}
.heading .script{color:var(--teal);font-size:86px;letter-spacing:0;margin-right:10px;vertical-align:-8px}

/* category cards */
.cat{width:300px;height:295px;background:var(--teal);text-decoration:none}
.cat .photo{position:absolute;left:7px;top:7px;width:286px;height:218px;background:linear-gradient(160deg,#8a5637,#5b3220 70%)}
.cat .label{position:absolute;left:23px;bottom:26px;right:23px;display:flex;justify-content:space-between;align-items:center;color:var(--white);font-size:16px;font-weight:600}
.cat .label svg{width:38px;height:14px}

.pill{height:45px;border-radius:23px;background:var(--teal);color:var(--white);font-size:15px;font-weight:600;display:flex;align-items:center;justify-content:center;letter-spacing:.3px}

/* about band */
.about{left:35px;top:1629px;width:1165px;height:461px;background:var(--teal);border-radius:230px 0 0 230px}
.about-circle{left:87px;top:1688px;width:332px;height:332px;border-radius:50%;background:var(--white);display:flex;flex-direction:column;align-items:center;justify-content:center;gap:14px}
.about-circle .mark{width:120px;height:120px;border-radius:50%;background:var(--teal)}
.about-circle .name{color:var(--teal);font-size:22px;font-weight:600;white-space:nowrap}
.about-name{left:448px;top:1742px;width:460px;text-align:center;color:var(--white);font-size:38px;font-weight:600;white-space:nowrap}
.about-text{left:448px;top:1846px;width:460px;text-align:center;color:var(--white);font-size:17px;line-height:25px}
.athlete{left:935px;top:1608px;width:265px;height:573px;background:linear-gradient(180deg,rgba(180,40,40,0) 0,#b62b2f 35%,#9b2226 70%,rgba(155,34,38,0) 100%);border-radius:40%}

/* products */
.product{width:295px;height:380px;background:#a6dde2}
.product .inner{position:absolute;left:11px;top:11px;right:11px;bottom:11px;background:linear-gradient(180deg,#2a98a4,#5fc3cd);text-align:center;color:var(--white)}
.product h3{font-size:20px;font-weight:600;margin-top:22px}
.product .sub{font-size:14px;margin-top:2px}
.product .price{font-size:24px;font-weight:700;margin-top:2px}
.product .btn-ghost{margin-top:12px;padding:5px 14px;font-size:15px}
.product .photo{position:absolute;left:70px;right:70px;bottom:0;height:190px;background:radial-gradient(ellipse at 50% 35%,#d8b27a 0,#7a4a2c 45%,rgba(122,74,44,0) 72%)}
.arrow{width:52px;height:52px;border-radius:50%;border:2px solid #333;display:flex;align-items:center;justify-content:center}
.arrow svg{width:18px;height:18px}

/* founder */
.founder{left:0;top:2852px;width:1200px;height:532px;background:var(--teal)}
.founder-photo{left:35px;top:2773px;width:462px;height:611px;background:linear-gradient(180deg,#e9f4f5 0,#6f4a36 30%,#1c1c1e 55%,#111 100%);border-radius:180px 180px 0 0}
.founder-title{left:562px;top:2945px;color:var(--white);font-size:34px;font-weight:600;white-space:nowrap}
.founder-title .script{font-size:86px;vertical-align:-10px;margin-right:10px}
.founder-text{left:562px;top:3054px;width:490px;color:var(--white);font-size:14px;line-height:26.5px}
.signature{left:562px;top:3232px;width:220px;height:60px;background:rgba(255,255,255,.35);border-radius:30px}

/* follow */
.gallery{width:231px;height:241px}
.g1{background:linear-gradient(160deg,#5a4032,#2f2119)}
.g2{background:linear-gradient(160deg,#c98b8f,#7b4a35)}
.g3{background:linear-gradient(160deg,#d9d3c9,#26406b)}
.g4{background:linear-gradient(160deg,#3a2b22,#a2866c)}

/* footer */
.footer-wave{left:0;top:3990px;width:1200px;height:90px}
.footer{left:0;top:4064px;width:1200px;height:430px;background:var(--teal-soft)}
.footer-logo{left:140px;top:4130px;width:156px;display:flex;flex-direction:column;align-items:center;gap:10px;color:var(--teal);font-size:18px;font-weight:600;text-align:center}
.footer-logo .mark{width:100px;height:100px;border-radius:50%;background:var(--teal)}
.fcol h4{font-size:24px;font-weight:600;color:#222;margin-bottom:18px}
.links a{display:block;font-size:14px;color:#333;text-decoration:none;line-height:29.5px}
.loc{display:flex;gap:14px;font-size:13.5px;line-height:19px;color:#333;margin-bottom:14px}
.loc .pin{flex:none;width:36px;height:36px;border-radius:50%;background:var(--teal);display:flex;align-items:center;justify-content:center}
.loc .pin svg{width:12px;height:16px}
.news p{font-size:14px;line-height:20px;color:#333;width:290px}
.news form{display:flex;margin-top:16px}
.news .email{width:165px;height:47px;background:var(--white);border:1px solid #cfe6e9;font-size:14px;padding-left:14px;line-height:45px;color:#333}
.news .sub{width:123px;height:47px;background:var(--teal);color:var(--white);font-size:14px;font-weight:700;text-align:center;line-height:47px}
.socials{display:flex;gap:12px;margin-top:20px}
.socials span{width:28px;height:28px;border-radius:50%;background:var(--teal)}
.rule{left:125px;top:4404px;width:950px;height:1px;background:#c8dfe2}
.copy{left:0;top:4433px;width:1200px;text-align:center;font-size:16px;color:#222}
</style>
</head>
<body>

<div class="abs topbar">
  <span>Locations: <svg viewBox="0 0 12 16"><path d="M6 0a6 6 0 0 0-6 6c0 4.5 6 10 6 10s6-5.5 6-10a6 6 0 0 0-6-6zm0 8.5A2.5 2.5 0 1 1 6 3.5a2.5 2.5 0 0 1 0 5z" fill="#fff"/></svg>2210 Cedar Row Dallas Texas</span>
  <span class="sep"></span>
  <span><svg viewBox="0 0 12 16"><path d="M6 0a6 6 0 0 0-6 6c0 4.5 6 10 6 10s6-5.5 6-10a6 6 0 0 0-6-6zm0 8.5A2.5 2.5 0 1 1 6 3.5a2.5 2.5 0 0 1 0 5z" fill="#fff"/></svg>4870 Willow Bend Pkwy Frisco Texas</span>
</div>

<header class="abs header">
  <div class="abs brand"><span class="brand-dot"></span>Marbrook Cupcakes</div>
  <div class="abs tools">
    <span><svg viewBox="0 0 24 24" style="width:14px;height:14px;vertical-align:-2px"><path d="M6.6 10.8a15 15 0 0 0 6.6 6.6l2.2-2.2a1 1 0 0 1 1-.25 11.4 11.4 0 0 0 3.6.6 1 1 0 0 1 1 1V20a1 1 0 0 1-1 1A17 17 0 0 1 3 4a1 1 0 0 1 1-1h3.5a1 1 0 0 1 1 1c0 1.25.2 2.45.6 3.6a1 1 0 0 1-.25 1z" fill="#72ccd4"/></svg> Call: 0824417390</span>
    <svg viewBox="0 0 24 24"><circle cx="10" cy="10" r="6.5" fill="none" stroke="#222" stroke-width="2.6"/><path d="M15 15l6 6" stroke="#222" stroke-width="2.8"/></svg>
    <svg viewBox="0 0 24 24"><circle cx="12" cy="8" r="5" fill="#222"/><path d="M3 22c0-5 4-8 9-8s9 3 9 8z" fill="#222"/></svg>
    <span class="cart"><svg viewBox="0 0 24 24"><path d="M2 3h3l3 12h11l3-9H7" fill="none" stroke="#222" stroke-width="2.4"/><circle cx="9" cy="20" r="2" fill="#222"/><circle cx="18" cy="20" r="2" fill="#222"/></svg><span class="count">0</span></span>
  </div>
  <nav class="abs nav">
    <a class="active" href="#">HOME</a><a href="#">SHOP ONLINE</a><a href="#">FLOVRS</a><a href="#">ABOUT ME</a><a href="#">BLOG</a><a href="#" style="margin-right:0">LOCATIONS</a>
  </nav>
</header>

<section class="abs hero">
  <div class="abs hero-brush"></div>
  <div class="abs hero-copy">
    <div class="line">SAVE 15% FOR</div>
    <div class="script">Valentine's Day</div>
    <div class="line">WITH LOVE25</div>
    <span class="btn-ghost">ONLINE ORDER</span>
  </div>
  <div class="abs hero-photo" role="img" aria-label="Two chocolate cupcakes with vanilla frosting and chocolate sprinkles on glass stands"></div>
  <div class="abs price-badge"><b>$6.00</b><span>PICK UP &amp;<br>DELIVERY</span></div>
</section>

<h2 class="abs heading" style="top:655px"><span class="script">Product</span>CATEGORIES</h2>

<a class="abs cat" style="left:127px;top:808px"><div class="photo" role="img" aria-label="Gourmet cupcakes with coconut pecan topping"></div><div class="label">GOURMET CUPCAKES<svg viewBox="0 0 38 14"><path d="M0 7h36M30 1l6 6-6 6" fill="none" stroke="#fff" stroke-width="1.6"/></svg></div></a>
<a class="abs cat" style="left:450px;top:808px"><div class="photo" role="img" aria-label="Cupcakes in jars with sprinkled frosting"></div><div class="label">CUPCAKE JARS<svg viewBox="0 0 38 14"><path d="M0 7h36M30 1l6 6-6 6" fill="none" stroke="#fff" stroke-width="1.6"/></svg></div></a>
<a class="abs cat" style="left:773px;top:808px"><div class="photo" role="img" aria-label="White frosted wedding cupcakes"></div><div class="label">WEDDING CAKES<svg viewBox="0 0 38 14"><path d="M0 7h36M30 1l6 6-6 6" fill="none" stroke="#fff" stroke-width="1.6"/></svg></div></a>
<a class="abs cat" style="left:127px;top:1130px"><div class="photo" role="img" aria-label="Cupcake with nut topping in a glass"></div><div class="label">YOUR FLAVORS<svg viewBox="0 0 38 14"><path d="M0 7h36M30 1l6 6-6 6" fill="none" stroke="#fff" stroke-width="1.6"/></svg></div></a>
<a class="abs cat" style="left:450px;top:1130px"><div class="photo" role="img" aria-label="Chocolate frosted cupcake"></div><div class="label">VALENTINE'S DAY<svg viewBox="0 0 38 14"><path d="M0 7h36M30 1l6 6-6 6" fill="none" stroke="#fff" stroke-width="1.6"/></svg></div></a>
<a class="abs cat" style="left:773px;top:1130px"><div class="photo" style="background:linear-gradient(160deg,#f0d7c6,#c97a5c 60%,#7a4a2c)" role="img" aria-label="Assorted birthday cupcakes seen from above"></div><div class="label">BIRTHDAY CUPCAKES<svg viewBox="0 0 38 14"><path d="M0 7h36M30 1l6 6-6 6" fill="none" stroke="#fff" stroke-width="1.6"/></svg></div></a>

<div class="abs pill" style="left:471px;top:1489px;width:258px">PICK UP AND DELIVERY</div>

<section class="abs about"></section>
<div class="abs about-circle"><span class="mark"></span><span class="name">Marbrook Cupcakes</span></div>
<div class="abs athlete" role="img" aria-label="Boy in a red basketball uniform leaping and holding up a cupcake"></div>
<div class="abs about-name">Marbrook Cupcakes</div>
<p class="abs about-text">Lorem ipsum dolor sit amet, consectetur adipiscing elit, sed do eiusmod tempor incididunt ut labore et dolore magna aliqua. Quis ipsum suspendisse ultrices gravida. Risus commodo viverra maecenas accumsan lacus vel facilisis.</p>

<h2 class="abs heading" style="top:2172px"><span class="script">Our</span>PRODUCTS</h2>

<div class="abs arrow" style="left:51px;top:2454px"><svg viewBox="0 0 18 18"><path d="M12 2L5 9l7 7" fill="none" stroke="#333" stroke-width="2"/></svg></div>
<div class="abs product" style="left:136px;top:2290px"><div class="inner"><h3>German Chocolate</h3><div class="sub">Pick up and Delivery</div><div class="price">$6.00</div><span class="btn-ghost">Online Order</span><div class="photo" role="img" aria-label="German chocolate cupcake on a glass stand"></div></div></div>
<div class="abs product" style="left:453px;top:2290px"><div class="inner"><h3>Caramel Peanut</h3><div class="sub">Pick up and Delivery</div><div class="price">$6.00</div><span class="btn-ghost">Online Order</span><div class="photo" role="img" aria-label="Caramel peanut cupcake on a glass stand"></div></div></div>
<div class="abs product" style="left:769px;top:2290px"><div class="inner"><h3>Lemon Cake</h3><div class="sub">Pick up and Delivery</div><div class="price">$6.00</div><span class="btn-ghost">Online Order</span><div class="photo" style="background:radial-gradient(ellipse at 50% 35%,#fbf4d0 0,#e9c25a 45%,rgba(233,194,90,0) 72%)" role="img" aria-label="Lemon cupcake with a lemon slice on a glass stand"></div></div></div>
<div class="abs arrow" style="left:1088px;top:2454px"><svg viewBox="0 0 18 18"><path d="M6 2l7 7-7 7" fill="none" stroke="#333" stroke-width="2"/></svg></div>

<section class="abs founder"></section>
<div class="abs founder-photo" role="img" aria-label="Portrait of the founder in a dark suit with arms crossed"></div>
<h2 class="abs founder-title"><span class="script">Meet</span>FOUNDER</h2>
<p class="abs founder-text">Lorem ipsum dolor sit amet, consectetur adipiscing elit, sed do eiusmod tempor incididunt ut labore et dolore magna aliqua. Quis ipsum suspendisse ultrices gravida. Risus commodo viverra maecenas accumsan lacus vel facilisis. Lorem ipsum dolor sit amet, consectetur adipiscing elit, sed do eiusmod tempor incididunt ut labore et dolore magna aliqua.</p>
<div class="abs signature" role="img" aria-label="Handwritten signature of Darren Hale"></div>

<h2 class="abs heading" style="top:3462px"><span class="script">Follow</span>MARBROOKCUPCAKES</h2>
<div class="abs gallery g1" style="left:122px;top:3579px" role="img" aria-label="Two cupcake jars on a dark table"></div>
<div class="abs gallery g2" style="left:365px;top:3579px" role="img" aria-label="Assorted cupcakes in a bakery box"></div>
<div class="abs gallery g3" style="left:607px;top:3579px" role="img" aria-label="Staff standing in the shop beside the display counter"></div>
<div class="abs gallery g4" style="left:849px;top:3579px" role="img" aria-label="Rows of cupcakes in a display case"></div>
<div class="abs pill" style="left:515px;top:3859px;width:170px">FOLLOW ME</div>

<svg class="abs footer-wave" viewBox="0 0 1200 90" preserveAspectRatio="none"><path d="M0 70Q600 -20 1200 70V90H0z" fill="var(--teal)"/><path d="M0 80Q600 0 1200 80V90H0z" fill="var(--teal-soft)"/></svg>
<footer class="abs footer"></footer>
<div class="abs footer-logo"><span class="mark"></span>Marbrook Cupcakes</div>
<div class="abs fcol links" style="left:366px;top:4120px"><h4>Links</h4><a href="#">About</a><a href="#">Reviews</a><a href="#">Shop</a><a href="#">Contact Us</a><a href="#">Blog</a></div>
<div class="abs fcol" style="left:506px;top:4120px">
  <h4>Locations</h4>
  <div class="loc"><span class="pin"><svg viewBox="0 0 12 16"><path d="M6 0a6 6 0 0 0-6 6c0 4.5 6 10 6 10s6-5.5 6-10a6 6 0 0 0-6-6zm0 8.5A2.5 2.5 0 1 1 6 3.5a2.5 2.5 0 0 1 0 5z" fill="#fff"/></svg></span><span>Location 1:<br>2210 Cedar Row Dallas Texas</span></div>
  <div class="loc"><span class="pin"><svg viewBox="0 0 12 16"><path d="M6 0a6 6 0 0 0-6 6c0 4.5 6 10 6 10s6-5.5 6-10a6 6 0 0 0-6-6zm0 8.5A2.5 2.5 0 1 1 6 3.5a2.5 2.5 0 0 1 0 5z" fill="#fff"/></svg></span><span>Location 2:<br>4870 Willow Bend Pkwy<br>Frisco Texas</span></div>
</div>
<div class="abs fcol news" style="left:785px;top:4120px">
  <h4>Newsletter</h4>
  <p>Receive access to VIP discounts, new product launches and more.</p>
  <form><div class="email">Email:</div><div class="sub">SUBSCRIBE</div></form>
  <div class="socials"><span></span><span></span><span></span><span></span></div>
</div>
<div class="abs rule"></div>
<p class="abs copy">Copyright © 2025 All rights reserved - Marbrook Cupcakes</p>

</body>
</html>
```